Verodex business card

Business card for sustainable investment company called "Verodex". Verodex is an exchange platform selling carbon credits between buyers and sellers. Carbon Credits are an environmental commodity for reducing global carbon emissions.

the card should obviously have our logo and the theme should be sustainability/environment mixed with a trading platform.

Contact Information for Business Card

Logo, Name, Title, Phone, Email

Colors
0054AA
0677BA
7BADD7
CADEEF
E8F1F8
0094D4
00A9DD
6FCCEA
C7EBF8
E9F6FB
00AB8E
00BBA5
67D7C9
C6EFE9
E9F9F6
59FF00
82FF00
B8FF75
E3FFCB
F4FFEA

```html
<!DOCTYPE html>
<html lang="en">
<head>
<meta charset="utf-8">
<title>Verodex business card</title>
<link rel="stylesheet" href="https://fonts.googleapis.com/css2?family=Montserrat:wght@400;500;600;700&display=swap">
<style>
  :root {
    --bg: #e6e8eb;
    --white: #ffffff;
    --navy: #1b2a4a;
    --ink: #1f2430;
    --sky: #33bde9;
    --aqua: #6ccbdc;
    --royal: #4470b8;
    --accent: #2fb4e6;
  }
  * { margin: 0; padding: 0; box-sizing: border-box; }
  html, body {
    width: 1200px; height: 900px; overflow: hidden;
    background: var(--bg);
    font-family: "Montserrat", sans-serif;
  }
  .stage {
    position: relative; width: 1200px; height: 900px;
  }
  .card {
    position: absolute; left: 250px; width: 700px; height: 400px;
    overflow: hidden;
    box-shadow: 0 6px 18px rgba(0,0,0,.12);
  }
  .card--front {
    top: 30px;
    background: linear-gradient(215deg, var(--royal) 0%, var(--sky) 50%, var(--aqua) 100%);
    display: flex; align-items: center; justify-content: center;
  }
  .brand {
    display: flex; align-items: center; gap: 22px;
  }
  .brand__dot {
    width: 46px; height: 46px; border-radius: 50%;
    background: var(--white);
  }
  .brand__name {
    color: var(--white); font-weight: 700; font-size: 64px;
    letter-spacing: 3px;
  }
  .card--back {
    top: 470px; background: var(--white);
  }
  .wave { position: absolute; inset: 0; }
  .back-brand {
    position: absolute; left: 60px; top: 118px;
    display: flex; align-items: center; gap: 16px;
  }
  .back-brand__dot {
    width: 30px; height: 30px; border-radius: 50%;
    background: var(--accent);
  }
  .back-brand__name {
    color: var(--navy); font-weight: 700; font-size: 40px; letter-spacing: 2px;
  }
  .person {
    position: absolute; right: 70px; top: 70px; text-align: right;
  }
  .person__name {
    font-weight: 700; font-size: 26px; color: var(--navy); letter-spacing: .5px;
  }
  .person__name span { color: var(--accent); }
  .person__title {
    font-size: 17px; color: var(--ink); margin-top: 4px;
  }
  .contacts {
    position: absolute; left: 88px; top: 218px; list-style: none;
  }
  .contacts li {
    display: flex; align-items: center; gap: 12px;
    font-size: 19px; color: var(--ink); line-height: 34px;
  }
  .contacts svg { width: 20px; height: 20px; flex: none; }
</style>
</head>
<body>
<main class="stage">
  <section class="card card--front" aria-label="Card front">
    <div class="brand">
      <span class="brand__dot"></span>
      <span class="brand__name">VERODEX</span>
    </div>
  </section>

  <section class="card card--back" aria-label="Card back">
    <svg class="wave" viewBox="0 0 700 400" preserveAspectRatio="none" aria-hidden="true">
      <defs>
        <linearGradient id="waveFill" x1="0" y1="1" x2="1" y2="0">
          <stop offset="0" stop-color="#6ccbdc"/>
          <stop offset=".5" stop-color="#33bde9"/>
          <stop offset="1" stop-color="#4470b8"/>
        </linearGradient>
      </defs>
      <path d="M240,400 C330,300 490,330 580,262 C640,215 665,130 700,66 L700,400 Z" fill="url(#waveFill)"/>
      <path d="M232,400 C322,296 484,322 574,254 C632,208 656,124 690,60" fill="none" stroke="#1b2a4a" stroke-width="5"/>
    </svg>

    <div class="back-brand">
      <span class="back-brand__dot"></span>
      <span class="back-brand__name">VERODEX</span>
    </div>

    <div class="person">
      <div class="person__name">DANIEL <span>HARTLEY</span></div>
      <div class="person__title">Co-Founder</div>
    </div>

    <ul class="contacts">
      <li>
        <svg viewBox="0 0 24 24" aria-hidden="true"><path fill="#2fb4e6" d="M6.6 10.8a15.1 15.1 0 0 0 6.6 6.6l2.2-2.2a1 1 0 0 1 1-.25 11.4 11.4 0 0 0 3.6.57 1 1 0 0 1 1 1V20a1 1 0 0 1-1 1A17 17 0 0 1 3 4a1 1 0 0 1 1-1h3.5a1 1 0 0 1 1 1c0 1.25.2 2.45.57 3.57a1 1 0 0 1-.25 1z"/></svg>
        308-555-0142
      </li>
      <li>
        <svg viewBox="0 0 24 24" aria-hidden="true"><rect x="2" y="5" width="20" height="14" rx="2" fill="#2fb4e6"/><path d="M2.5 6l9.5 7 9.5-7" fill="none" stroke="#fff" stroke-width="1.6"/></svg>
        info@verodex.com
      </li>
      <li>
        <svg viewBox="0 0 24 24" aria-hidden="true"><circle cx="12" cy="12" r="10" fill="#2fb4e6"/><path d="M2 12h20M12 2c3 3 3 17 0 20M12 2c-3 3-3 17 0 20" fill="none" stroke="#fff" stroke-width="1.3"/></svg>
        www.verodex.com
      </li>
    </ul>
  </section>
</main>
</body>
</html>
```